Luxury Business Card Design for High-End Window Treatments

Gilded Slatworks
Custom Plantation Shutters & Architectural Shading Systems

⸻

BACK

Daniel Trevick
Owner

Custom Interior & Exterior Window Treatments

919-555-0148
gildedslatworks.com

I have included a picture that I’m hoping we can use on the back, but I’m also wondering if you can get rid of the ladder? Should we get rid of shutters , shades and blinds underneath Gilded Slatworks?

Target Market(s)

High-end residential homeowners, custom home builders, architects, interior designers, and luxury renovation clients seeking premium plantation shutters and motorized architectural shading systems.

Industry/Entity Type

Custom Window treatments

Contact Information for Business Card

Front Gilded Slatworks Custom Plantation Shutters Motorized Architectural Shading Systems BACK Daniel Trevick Owner 919-555-0148 GildedSlatworks.com Custom Interior & Exterior Window Treatments By Appointment

Requirements
Nice to have
• Not 100% sure on nice to halves or the color but you can definitely check out my website to get a better understanding of what I’m trying to do

```html
<!DOCTYPE html>
<html lang="en">
<head>
<meta charset="utf-8">
<title>Gilded Slatworks — Business Card</title>
<link rel="stylesheet" href="https://fonts.googleapis.com/css2?family=Open+Sans:wght@300;400;700&family=Alegreya:wght@700&display=swap">
<style>
  :root {
    --backdrop: #e8e7e4;
    --card-black: #1c1b1a;
    --gold: #e6c14a;
    --gold-edge: #c9a43a;
    --ivory: #ece8dc;
    --soft-white: #dedbd3;
    --sky: #5a92e0;
    --house-dark: #2a3140;
    --foliage: #4d5a36;
  }
  * { box-sizing: border-box; margin: 0; padding: 0; }
  html, body { width: 1200px; height: 801px; overflow: hidden; }
  body {
    background: var(--backdrop);
    font-family: "Open Sans", Arial, sans-serif;
    position: relative;
  }
  .card {
    position: absolute;
    top: 246px;
    width: 540px;
    height: 309px;
    background: var(--card-black);
    border-bottom: 4px solid var(--gold-edge);
    overflow: hidden;
    box-shadow: 0 14px 30px rgba(0,0,0,0.18);
  }
  .card--back { left: 36px; }
  .card--front { left: 624px; }

  /* Back side */
  .card__photo {
    position: absolute;
    inset: 0;
    clip-path: polygon(0 0, 100% 0, 100% 72%, 0 30%);
    background: linear-gradient(160deg, var(--sky) 0%, #7fa9e4 30%, var(--house-dark) 58%, var(--foliage) 100%);
  }
  .back__content {
    position: absolute;
    left: 30px;
    bottom: 22px;
    width: 330px;
  }
  .brand-name {
    font-family: "Open Sans", Arial, sans-serif;
    font-weight: 300;
    color: var(--ivory);
    line-height: 1.05;
  }
  .back__content .brand-name { font-size: 28px; }
  .product-line {
    font-family: "Alegreya", Georgia, serif;
    font-weight: 700;
    color: var(--gold);
    word-spacing: 10px;
  }
  .back__content .product-line { font-size: 13px; margin: 4px 0 10px; }
  .person__name {
    font-weight: 700;
    color: var(--gold);
    font-size: 17px;
    letter-spacing: 0.5px;
    text-transform: uppercase;
  }
  .person__role {
    color: var(--soft-white);
    font-size: 13px;
    margin-bottom: 6px;
  }
  .rule {
    width: 22px;
    height: 1px;
    background: var(--gold);
    margin: 4px 0;
  }
  .contact {
    list-style: none;
    color: var(--soft-white);
    font-size: 13px;
    line-height: 1.45;
  }
  .contact li { display: flex; align-items: center; gap: 6px; }
  .contact svg { width: 11px; height: 11px; fill: var(--gold); flex: none; }
  .services {
    color: var(--soft-white);
    font-size: 13px;
    line-height: 1.35;
  }

  /* Front side */
  .front__content {
    position: absolute;
    inset: 0;
    display: flex;
    flex-direction: column;
    align-items: center;
    justify-content: center;
    text-align: center;
  }
  .front__content .brand-name { font-size: 44px; }
  .front__content .product-line { font-size: 21px; margin: 8px 0 20px; word-spacing: 16px; }
  .front__tagline {
    color: var(--soft-white);
    font-size: 15px;
    line-height: 1.4;
  }
</style>
</head>
<body>

<section class="card card--back" aria-label="Business card back">
  <div class="card__photo" role="img" aria-label="Photograph of a two-storey home with dark exterior shades, white columns, pine trees and a blue sky"></div>
  <div class="back__content">
    <p class="brand-name">Gilded Slatworks</p>
    <p class="product-line">Shutters Shades Blinds</p>
    <p class="person__name">Daniel Trevick</p>
    <p class="person__role">Owner</p>
    <div class="rule"></div>
    <ul class="contact">
      <li>
        <svg viewBox="0 0 24 24" aria-hidden="true"><path d="M6.6 10.8a15.2 15.2 0 0 0 6.6 6.6l2.2-2.2a1 1 0 0 1 1-.25 11.4 11.4 0 0 0 3.6.57 1 1 0 0 1 1 1V20a1 1 0 0 1-1 1A17 17 0 0 1 3 4a1 1 0 0 1 1-1h3.5a1 1 0 0 1 1 1c0 1.25.2 2.45.57 3.6a1 1 0 0 1-.25 1z"/></svg>
        919-555-0148
      </li>
      <li>
        <svg viewBox="0 0 24 24" aria-hidden="true"><circle cx="12" cy="12" r="10"/></svg>
        gildedslatworks.com
      </li>
    </ul>
    <div class="rule"></div>
    <p class="services">Custom Interior &amp;<br>Exterior Window Treatments</p>
  </div>
</section>

<section class="card card--front" aria-label="Business card front">
  <div class="front__content">
    <p class="brand-name">Gilded Slatworks</p>
    <p class="product-line">Shutters Shades Blinds</p>
    <p class="front__tagline">Custom Plantation Shutters &amp;<br>Motorized Architectural Shading Systems</p>
  </div>
</section>

</body>
</html>
```